Poster for Kirtan Music Event

Design (3) 24" x 36" Posters

I have provided a sample a friend did in Australia: ( Picture No. 4 )

Use all the text on sample poster except the replacement changes below.

Replace with the following text as this is for different location:
Replacement Text:

Every Friday Night 7:00pm-8:30pm
Kealoha Pilates & Movement Studio
947 Hollister Rd Paia

Free Kirtan Experience! or Free Event
Mohan Priya Sevi & Companions

Optional Text:

A evening of music, singing of spiritual mantras, and refreshments

Bring flowers, musical instruments, friends, or just come with an open heart.

Meditate on transcendental sounds that provide rest for the mind & heart"

An evening of music & singing of sacred mantra's

```html
<!DOCTYPE html>
<html lang="en">
<head>
<meta charset="utf-8">
<title>Kirtan Experience Poster</title>
<link rel="stylesheet" href="https://fonts.googleapis.com/css2?family=Oswald:wght@300;400;700&family=Pathway+Gothic+One&family=Dosis:wght@500;600&display=swap">
<style>
  :root {
    --bg-deep: #141414;
    --bg-mid: #2b2b2b;
    --bg-soft: #3a3a3a;
    --peach: #f2a987;
    --peach-line: #e9a283;
    --rust-box: rgba(150, 78, 42, 0.85);
    --gold: #c9962e;
    --white: #ffffff;
    --text-soft: #f3f3f3;
  }
  * { margin: 0; padding: 0; box-sizing: border-box; }
  html, body { width: 800px; height: 1200px; overflow: hidden; background: var(--bg-deep); }
  .poster {
    position: relative;
    width: 800px;
    height: 1200px;
    overflow: hidden;
    background:
      linear-gradient(160deg, rgba(255,255,255,0.06) 0%, transparent 35%),
      linear-gradient(20deg, rgba(255,255,255,0.05) 0%, transparent 40%),
      radial-gradient(ellipse at 50% 40%, var(--bg-soft) 0%, var(--bg-mid) 40%, var(--bg-deep) 100%);
    font-family: "Pathway Gothic One", "Oswald", sans-serif;
    color: var(--white);
  }
  .lotus-glow {
    position: absolute;
    left: 60px; top: 40px;
    width: 680px; height: 700px;
    background: radial-gradient(circle at 50% 50%, rgba(160, 80, 45, 0.28) 0%, rgba(120, 60, 35, 0.15) 45%, transparent 70%);
  }
  .rule {
    position: absolute;
    left: 66px; right: 62px;
    height: 2px;
    background: var(--peach-line);
  }
  .rule-top { top: 53px; }
  .rule-bottom { top: 1149px; }
  .flourish {
    position: absolute;
    left: 310px;
    width: 180px; height: 30px;
    background: linear-gradient(90deg, var(--bg-deep), var(--peach-line) 50%, var(--bg-deep));
    opacity: 0.85;
    border-radius: 15px;
  }
  .flourish-top { top: 39px; }
  .flourish-bottom { top: 1135px; }
  .performers {
    position: absolute;
    left: 40px; top: 168px;
    width: 640px; height: 400px;
    background: radial-gradient(ellipse at 50% 45%, #9a9a9a 0%, #6a6a6a 40%, rgba(40,40,40,0.2) 80%, transparent 100%);
  }
  .tagline {
    position: absolute;
    line-height: 1.25;
    text-align: center;
    color: var(--text-soft);
    background: var(--rust-box);
    border-radius: 12px 4px 12px 4px;
    box-shadow: 0 0 14px rgba(0,0,0,0.5);
  }
  .tagline-invite { left: 22px; top: 82px; width: 242px; height: 192px; padding: 22px 4px; font-size: 23px; }
  .tagline-evening { left: 612px; top: 786px; width: 170px; height: 148px; padding: 16px 8px; font-size: 23px; }
  .title-band {
    position: absolute;
    left: 0; top: 590px;
    width: 800px; height: 160px;
    background: linear-gradient(180deg, rgba(0,0,0,0.1), rgba(0,0,0,0.75) 20%, rgba(0,0,0,0.75) 80%, rgba(0,0,0,0.1));
  }
  .seal { position: absolute; left: 230px; top: 520px; }
  .title {
    position: absolute;
    left: 0; top: 602px;
    width: 800px;
    height: 134px;
    text-align: center;
    white-space: nowrap;
    font-family: "Oswald", sans-serif;
    font-weight: 700;
    font-size: 84px;
    line-height: 134px;
    letter-spacing: 3px;
    transform: scaleY(1.45);
    transform-origin: 50% 50%;
    background: linear-gradient(180deg, #ffffff 0%, #e6e6e6 45%, #8f8f8f 52%, #f2f2f2 70%, #ffffff 100%);
    -webkit-background-clip: text;
    background-clip: text;
    color: transparent;
    filter: drop-shadow(4px 1px 0 var(--gold));
  }
  .details {
    position: absolute;
    left: 0; width: 800px;
    text-align: center;
  }
  .detail-small { font-family: "Pathway Gothic One", sans-serif; font-size: 20px; color: var(--text-soft); }
  .free { top: 868px; }
  .hosts { top: 900px; }
  .stars { font-size: 14px; letter-spacing: 4px; color: var(--white); }
  .stars-1 { top: 932px; }
  .schedule {
    top: 952px;
    font-family: "Dosis", sans-serif;
    font-weight: 600;
    font-size: 41px;
    color: var(--peach);
  }
  .stars-2 { top: 1010px; }
  .venue, .address { font-family: "Pathway Gothic One", sans-serif; font-size: 25px; color: var(--text-soft); }
  .venue { top: 1034px; }
  .address { top: 1069px; }
  .stars-3 { top: 1106px; }
  .page-curl { position: absolute; right: 0; bottom: 0; }
</style>
</head>
<body>
  <main class="poster">
    <div class="lotus-glow" role="img" aria-label="Faint large lotus decoration in warm rust tones"></div>

    <div class="rule rule-top"></div>
    <div class="flourish flourish-top" role="img" aria-label="Peach ornamental scroll"></div>

    <div class="performers" role="img" aria-label="Photo of two musicians singing kirtan, one with guitar and microphone, one playing harmonium"></div>

    <p class="tagline tagline-invite">Join us in the singing<br>of transcendental sounds<br>that provide rest<br>for the mind &amp; heart</p>

    <div class="title-band"></div>
    <svg class="seal" width="340" height="340" viewBox="0 0 340 340" aria-hidden="true">
      <circle cx="170" cy="170" r="164" fill="none" stroke="#1b1b1b" stroke-width="6"/>
      <circle cx="170" cy="170" r="148" fill="none" stroke="#6a6a6a" stroke-width="2" stroke-dasharray="2 9"/>
      <circle cx="170" cy="170" r="134" fill="none" stroke="#1b1b1b" stroke-width="3"/>
    </svg>
    <h1 class="title">KIRTAN EXPERIENCE</h1>

    <p class="tagline tagline-evening">An evening of<br>music &amp; singing<br>of sacred<br>mantra's</p>

    <p class="details detail-small free">Free Event!</p>
    <p class="details detail-small hosts">Mohan Priya Sevi &amp; Companions</p>
    <p class="details stars stars-1">★★★</p>
    <p class="details schedule">Every Friday Night 7:00pm-8:30pm</p>
    <p class="details stars stars-2">★★★</p>
    <p class="details venue">Kealoha Pilates &amp; Movement Studio</p>
    <p class="details address">947 Hollister Rd Paia</p>
    <p class="details stars stars-3">★★★</p>

    <div class="rule rule-bottom"></div>
    <div class="flourish flourish-bottom" role="img" aria-label="Peach ornamental scroll"></div>

    <svg class="page-curl" width="60" height="60" viewBox="0 0 60 60" aria-hidden="true">
      <path d="M60 0 L60 60 L0 60 Z" fill="#ffffff"/>
      <path d="M60 0 Q30 20 0 60 Q40 45 60 0 Z" fill="#d8d8d8"/>
    </svg>
  </main>
</body>
</html>
```